copper vale energy ltd commercial solar installs

a bifold A4 brochure , explaining the benefits of solar panel and battery storage on commercial buildings in England

i dont have many images or paragraphs i was hoping that this could be part of your design

```html
<!DOCTYPE html>
<html lang="en">
<head>
<meta charset="utf-8">
<title>Copper Vale Energy Ltd – Commercial Solar Brochure</title>
<link href="https://fonts.googleapis.com/css2?family=Montserrat:wght@400;500;600;700;800&display=swap" rel="stylesheet">
<style>
  :root {
    --green: #3db83a;
    --green-dark: #2e9a2c;
    --ink: #1c1c1c;
    --dark: #141414;
    --paper: #f7f7f6;
    --stage: #d9d9dc;
    --text-light: #e9e9e9;
  }
  * { box-sizing: border-box; margin: 0; padding: 0; }
  html, body { width: 1200px; height: 840px; overflow: hidden; }
  body {
    background: var(--stage);
    font-family: "Montserrat", sans-serif;
    display: flex; align-items: center; justify-content: center;
  }
  .spread { display: flex; width: 1120px; height: 792px; box-shadow: 0 10px 30px rgba(0,0,0,.18); }
  .page { position: relative; width: 560px; height: 792px; overflow: hidden; }

  /* Inside left */
  .page--about { background: var(--paper); color: var(--ink); }
  .section-title {
    color: var(--green); font-weight: 800; text-transform: uppercase;
    font-size: 24px; letter-spacing: .5px;
  }
  .about { position: absolute; left: 48px; top: 56px; width: 460px; }
  .about p { margin-top: 16px; font-size: 13.5px; line-height: 1.6; font-weight: 500; }
  .why { position: absolute; left: 48px; top: 270px; width: 250px; }
  .why-list { list-style: none; margin-top: 18px; }
  .why-list li {
    position: relative; padding-left: 26px; margin-bottom: 14px;
    font-size: 12.5px; line-height: 1.55; font-weight: 500;
  }
  .why-list svg { position: absolute; left: 0; top: 2px; }
  .worker-photo {
    position: absolute; right: 0; top: 250px; width: 240px; height: 430px;
    border-radius: 0 0 0 22px;
    background: linear-gradient(160deg, #9fb3c9 0%, #3a4a66 35%, #22314a 60%, #b7c23a 80%, #3b2b22 100%);
  }
  .band { position: absolute; left: 0; top: 700px; width: 100%; height: 14px; background: var(--green); }
  .brand {
    position: absolute; right: 36px; bottom: 28px;
    display: flex; align-items: center; gap: 10px;
    font-weight: 700; font-size: 13px; line-height: 1.2;
  }
  .brand-mark { width: 22px; height: 22px; background: var(--green); border-radius: 3px; }

  /* Inside right */
  .page--benefits { background: var(--dark); color: var(--text-light); }
  .panels-photo {
    position: absolute; left: 0; top: 0; width: 100%; height: 230px;
    background: linear-gradient(200deg, #f4d9b8 0%, #c7d3ea 18%, #4a6fb0 45%, #1d3366 80%, #141414 100%);
  }
  .benefits-title {
    position: absolute; left: 48px; top: 252px; width: 470px;
    font-size: 24px; font-weight: 800; text-transform: uppercase; color: #fff; line-height: 1.2;
  }
  .benefit-list { position: absolute; left: 48px; top: 326px; width: 470px; list-style: none; }
  .benefit { display: flex; gap: 16px; margin-bottom: 16px; }
  .benefit-icon {
    flex: none; width: 40px; height: 40px; border-radius: 8px; background: var(--green);
    display: flex; align-items: center; justify-content: center;
  }
  .benefit h3 { color: var(--green); font-size: 14px; font-weight: 700; margin-bottom: 3px; }
  .benefit p { font-size: 11px; line-height: 1.45; }
  .page--benefits .brand { color: #fff; }
</style>
</head>
<body>
<main class="spread">

  <section class="page page--about">
    <div class="about">
      <h2 class="section-title">About Us</h2>
      <p>Copper Vale Energy is a trusted solar installer serving southeast England since 2008. Our qualified experts have over 15 years experience helping homeowners and businesses transition to affordable sustainable solar power.</p>
    </div>

    <div class="why">
      <h2 class="section-title">Why Choose Us?</h2>
      <ul class="why-list">
        <li><svg width="16" height="16" viewBox="0 0 16 16"><rect width="16" height="16" rx="3" fill="#3db83a"/><path d="M4 8.5l2.5 2.5L12 5.5" stroke="#fff" stroke-width="2" fill="none"/></svg>Over 1,000 solar systems installed across residential and commercial properties.</li>
        <li><svg width="16" height="16" viewBox="0 0 16 16"><rect width="16" height="16" rx="3" fill="#3db83a"/><path d="M4 8.5l2.5 2.5L12 5.5" stroke="#fff" stroke-width="2" fill="none"/></svg>We handle the full process: consultations, approval, installations and maintenance.</li>
        <li><svg width="16" height="16" viewBox="0 0 16 16"><rect width="16" height="16" rx="3" fill="#3db83a"/><path d="M4 8.5l2.5 2.5L12 5.5" stroke="#fff" stroke-width="2" fill="none"/></svg>Approved member of the Kestrel Solar Guild and Brightfield Energy Network.</li>
        <li><svg width="16" height="16" viewBox="0 0 16 16"><rect width="16" height="16" rx="3" fill="#3db83a"/><path d="M4 8.5l2.5 2.5L12 5.5" stroke="#fff" stroke-width="2" fill="none"/></svg>Experts stay up-to-date with latest advances in solar technology.</li>
        <li><svg width="16" height="16" viewBox="0 0 16 16"><rect width="16" height="16" rx="3" fill="#3db83a"/><path d="M4 8.5l2.5 2.5L12 5.5" stroke="#fff" stroke-width="2" fill="none"/></svg>Finance options are available and payback times are greatly reduced.</li>
      </ul>
    </div>

    <div class="worker-photo" role="img" aria-label="Photo of an installer in a hard hat and hi-vis vest fitting solar panels"></div>
    <div class="band"></div>
    <div class="brand"><span class="brand-mark"></span><span>Copper Vale<br>Energy Ltd</span></div>
  </section>

  <section class="page page--benefits">
    <div class="panels-photo" role="img" aria-label="Photo of solar panel array with sunlight glare"></div>
    <h2 class="benefits-title">Benefits of Solar Panels<br>&amp; Battery Storage</h2>

    <ul class="benefit-list">
      <li class="benefit">
        <span class="benefit-icon"><svg width="22" height="22" viewBox="0 0 22 22" fill="none" stroke="#fff" stroke-width="1.6"><circle cx="11" cy="11" r="8"/><path d="M13.5 7.5a2.5 2.5 0 0 0-4.5 1.5v6M7.5 12h5M7.5 15h7"/></svg></span>
        <div><h3>Financial Savings</h3><p>Cut electricity by 50-90% with solar.<br>Earn extra revenue by exporting excess energy to the grid.<br>Use battery storage to utilize energy later instead of sending back to grid.</p></div>
      </li>
      <li class="benefit">
        <span class="benefit-icon"><svg width="22" height="22" viewBox="0 0 22 22" fill="none" stroke="#fff" stroke-width="1.6"><path d="M5 17C5 9 10 5 18 4c0 8-4 13-12 13z"/><path d="M5 17l7-7"/></svg></span>
        <div><h3>Sustainability</h3><p>Reduce carbon footprint by using clean renewable solar power.<br>Help address climate change by minimizing fossil fuel use.<br>Enhance corporate social responsibility through renewable energy.</p></div>
      </li>
      <li class="benefit">
        <span class="benefit-icon"><svg width="22" height="22" viewBox="0 0 22 22" fill="#fff"><path d="M12 2L5 12h5l-1 8 7-10h-5z"/></svg></span>
        <div><h3>Resilience</h3><p>Add energy security through onsite solar electricity generation.<br>Avoid issues with traditional grid by producing your own power.<br>Battery systems provide backup electricity during outages.</p></div>
      </li>
      <li class="benefit">
        <span class="benefit-icon"><svg width="22" height="22" viewBox="0 0 22 22" fill="none" stroke="#fff" stroke-width="1.6"><path d="M3 11V4h7l9 9-7 7z"/><circle cx="7" cy="8" r="1.5" fill="#fff"/></svg></span>
        <div><h3>Incentives</h3><p>Tax allowance and export guarantee payments incentivize solar investments.<br>Interest free loans and grants improve affordability.<br>Certified professionals ensure quality support.</p></div>
      </li>
    </ul>

    <div class="band"></div>
    <div class="brand"><span class="brand-mark"></span><span>Copper Vale<br>Energy Ltd</span></div>
  </section>

</main>
</body>
</html>
```